MEDICAL CLINIC LETTERHEAD

Design is a letterhead for a non-profit medical center. The name of the clinic is VITARIDGE Community Health Center. Although the full name must be included, the community health center part is more of a description and should be less visible - i attached an example of what I mean by that (ATTACHED IMAGE IS AN EXAMPLE OF FONT SIZES NOT A DESIGN IDEA). Please design something modern, cool looking and unique because I can always download free templates.
Phone, email, website and etc will be added later.

Industry/Entity Type

MEDICAL

```html
<!DOCTYPE html>
<html lang="en">
<head>
<meta charset="utf-8">
<title>VITARIDGE Letterhead</title>
<link href="https://fonts.googleapis.com/css2?family=Questrial&family=Montserrat:wght@400;600&family=Open+Sans:wght@600&display=swap" rel="stylesheet">
<style>
  :root {
    --navy: #172c55;
    --gold: #a88a55;
    --text-grey: #8e8f93;
    --heading-grey: #9a9b9e;
    --paper: #ffffff;
    --signature-tone: #e9e9eb;
  }
  html, body { margin: 0; padding: 0; overflow: hidden; background: #f2f2f2; }
  .letterhead {
    position: relative;
    width: 908px;
    height: 1200px;
    background: var(--paper);
    overflow: hidden;
    font-family: "Questrial", sans-serif;
    color: var(--text-grey);
  }
  .brand { position: absolute; left: 36px; top: 72px; }
  .brand-name {
    display: block;
    font-size: 40px;
    line-height: 1;
    color: var(--navy);
    letter-spacing: 0.5px;
  }
  .brand-descriptor {
    display: block;
    margin-top: 4px;
    font-size: 8.5px;
    color: var(--gold);
    letter-spacing: 0.2px;
  }
  .recipient {
    position: absolute;
    left: 41px;
    top: 283px;
    font-family: "Montserrat", sans-serif;
  }
  .recipient-name {
    margin: 0 0 6px;
    font-weight: 600;
    font-size: 24px;
    line-height: 30px;
    color: var(--heading-grey);
    letter-spacing: 0.5px;
  }
  .recipient-line {
    margin: 0 0 7px;
    font-size: 13.5px;
    line-height: 20px;
  }
  .recipient-address {
    margin: 0;
    font-size: 13.5px;
    line-height: 21px;
  }
  .letter-date {
    position: absolute;
    right: 42px;
    top: 389px;
    margin: 0;
    font-family: "Open Sans", sans-serif;
    font-weight: 600;
    font-size: 16px;
    line-height: 22px;
    color: var(--text-grey);
  }
  .letter-body {
    position: absolute;
    left: 36px;
    width: 830px;
    margin: 0;
    font-size: 16.6px;
    line-height: 19.8px;
    letter-spacing: -0.3px;
    text-align: justify;
  }
  .body-one { top: 450px; }
  .body-two { top: 588px; }
  .body-three { top: 726px; }
  .signatory-title {
    position: absolute;
    left: 629px;
    top: 834px;
    margin: 0;
    font-size: 22px;
    line-height: 28px;
    color: var(--text-grey);
  }
  .signature {
    position: absolute;
    left: 649px;
    top: 884px;
    width: 167px;
    height: 98px;
    background: var(--signature-tone);
    border-radius: 4px;
  }
  .contact-band {
    position: absolute;
    left: 0;
    top: 1133px;
    width: 776px;
    height: 35px;
    background: var(--navy);
    border-radius: 0 18px 18px 0;
  }
  .contact-item {
    position: absolute;
    top: 0;
    height: 35px;
    display: flex;
    align-items: center;
    gap: 6px;
    color: #ffffff;
    font-size: 18px;
  }
  .contact-item svg { width: 14px; height: 14px; flex: none; }
  .item-phone { left: 62px; }
  .item-email { left: 225px; }
  .item-web { left: 472px; }
</style>
</head>
<body>
<main class="letterhead">
  <header class="brand">
    <span class="brand-name">VITARIDGE</span>
    <span class="brand-descriptor">COMMUNITY HEALTH CENTER</span>
  </header>

  <section class="recipient">
    <h1 class="recipient-name">JANE MERROW</h1>
    <p class="recipient-line">0100-555-214</p>
    <p class="recipient-line">info@northlanepost.com</p>
    <p class="recipient-address">4410 Cedar Loop Ln. Suite<br>210 Plano, TX 0000</p>
  </section>

  <p class="letter-date">12 December, 2023</p>

  <p class="letter-body body-one">Lorem ipsum dolor sit amet, consectetuer adipiscing elit, sed diam nonummy nibh euismod tincidunt ut laoreet dolore magna aliquam erat volutpat. Ut wisi enim ad minim veniam, quis nostrud exerci tation ulla&shy;mcorper suscipit lobortis nisl ut aliquip ex ea commodo consequat. Duis autem vel eum iriure dolor in hen&shy;drerit in vulputate velit esse molestie consequat, vel illum dolore eu feugiat nulla facilisis at vero eros et accumsan et iusto odio dignissim qui blandit praesent luptatum zzril delenit augue duis dolore te feugait nulla facilisi.</p>

  <p class="letter-body body-two">Lorem ipsum dolor sit amet, cons ectetuer adipiscing elit, sed diam nonummy nibh euismod tincidunt ut laoreet dolore magna aliquam erat volutpat. Ut wisi enim ad minim veniam, quis nostrud exerci tation ulla&shy;mcorper suscipit lobortis nisl ut aliquip ex ea commodo consequat.<br>Lorem ipsum dolor sit amet, consectetuer adipiscing elit, sed diam nonummy nibh euismod tincidunt ut laoreet dolore magna aliquam erat</p>

  <p class="letter-body body-three">Lorem ipsum dolor sit amet, cons ectetuer adipiscing elit, sed diam nonummy nibh euismod tincidunt ut laoreet dolore magna aliquam erat volutpat. Ut wisi enim ad minim veniam, quis nostrud exerci tation ulla&shy;mcorper suscipit lobortis nisl ut aliquip ex ea commodo consequat. Lorem ipsum dolor sit zamet, consec&shy;tetuer adipiscing elit, sed diam nonummy nibh euismod tincidunt.</p>

  <p class="signatory-title">Managing Director</p>
  <div class="signature" role="img" aria-label="Handwritten signature of the managing director"></div>

  <footer class="contact-band">
    <span class="contact-item item-phone">
      <svg viewBox="0 0 14 14" aria-hidden="true"><circle cx="7" cy="7" r="7" fill="#a88a55"/><path d="M4.6 3.6l1.3 1.4-.7.9c.5 1 1.3 1.8 2.3 2.3l.9-.7 1.4 1.3-.8 1c-2.6-.3-4.9-2.6-5.2-5.2z" fill="#172c55"/></svg>
      0100-555-214
    </span>
    <span class="contact-item item-email">
      <svg viewBox="0 0 14 14" aria-hidden="true"><circle cx="7" cy="7" r="7" fill="#a88a55"/><rect x="3.5" y="4.5" width="7" height="5" fill="none" stroke="#172c55" stroke-width="1"/><path d="M3.5 4.5L7 7.3l3.5-2.8" fill="none" stroke="#172c55" stroke-width="1"/></svg>
      info@vitaridge.com
    </span>
    <span class="contact-item item-web">
      <svg viewBox="0 0 14 14" aria-hidden="true"><circle cx="7" cy="7" r="7" fill="#a88a55"/><circle cx="7" cy="7" r="3.8" fill="none" stroke="#172c55" stroke-width="0.9"/><ellipse cx="7" cy="7" rx="1.6" ry="3.8" fill="none" stroke="#172c55" stroke-width="0.9"/><path d="M3.2 7h7.6" stroke="#172c55" stroke-width="0.9"/></svg>
      www.vitaridge.com
    </span>
  </footer>
</main>
</body>
</html>
```